Product label for premium fruit wooden crates

Background: TavoNest offers premium quality fruits airflown (i.e. Japan, USA, Australia, etc) to Singapore at an affordable price. This includes exquisite and limited fruits like Velra Dusk grape, Harimoto Lantern Melon, Yellow Dragon Fruit, Lan bo tu seedless lychee, Yellow Peaches, etc.

Requirements:

- Design a premium fruit’s label strap for identification and brand marketing.

- This strap will be used to tie around our fruit gift crate and fruit boxes (see attached).

- the logo use in this strap may use different color that must fit the 2 ribbons that will be used together with the crate box (see attached), red and gold ribbons(purl satin)

- the fruit crates and boxes will be presented as gift for vip, families, and working partners (important people)

This label will be printed in paper and tie around the fruit crate or paper box.

Web: www.tavonest.sg
FB: https://www.facebook.com/tvnharvest/
IG: https://www.instagram.com/tvnharvest

Target Market(s)

Working class, families, expat, business clients (late 20 – 40s)

Industry/Entity Type

Gift Shop

Font styles to use
Other font styles liked:
• Sakkal Majalla

Requirements
Must have
• - color that fit the 2 ribbons color (red and gold)
• - premium, luxury and exquisite feel
• - presentable as a gift to someone important
• - Tavonest's logo
• - The word 'TAVONEST',
Nice to have
• the following words:
• - www.tavonest.sg; or/and
• - online premium fruits or/and
• - premium quality (No preference. let the designer choose)
• must be able to give customer a feel that Tavonest sells premium fruits
Should not have
• cant think of it now

```html
<!DOCTYPE html>
<html lang="en">
<head>
<meta charset="utf-8">
<title>TavoNest Crate Strap</title>
<link href="https://fonts.googleapis.com/css2?family=Josefin+Sans:wght@300&display=swap" rel="stylesheet">
<style>
  :root {
    --page: #ffffff;
    --pink-light: #fad3da;
    --pink-mid: #f7b8c4;
    --pink-deep: #f4a1b1;
    --pattern-a: #fbdde3;
    --pattern-b: #f6c3cd;
    --brand: #ef6f86;
    --gold-dark: #c98a1e;
    --gold-light: #f6e08a;
    --olive: #b8b06a;
  }
  * { margin: 0; padding: 0; box-sizing: border-box; }
  html, body { width: 1200px; height: 459px; overflow: hidden; background: var(--page); }
  .canvas { position: relative; width: 1200px; height: 459px; font-family: "Josefin Sans", sans-serif; }

  .strap { position: absolute; overflow: hidden; background: var(--pink-light); }
  .strap-pattern {
    position: absolute; inset: 0;
    background: linear-gradient(100deg, var(--pattern-a), var(--pattern-b) 30%, var(--pattern-a) 55%, var(--pattern-b) 80%, var(--pattern-a));
  }
  .panel { position: absolute; top: 0; bottom: 0; background: var(--pink-deep); opacity: .75; }
  .panel.mid { background: var(--pink-mid); opacity: .8; }
  .trim { position: absolute; left: 0; right: 0; }
  .trim-gold { background: linear-gradient(90deg, var(--gold-dark), var(--gold-light) 35%, var(--gold-dark) 60%, var(--gold-light) 85%, var(--gold-dark)); }
  .trim-olive { background: var(--olive); }

  .brand { position: absolute; display: flex; align-items: center; color: var(--brand); font-weight: 300; white-space: nowrap; }
  .brand-dot { border-radius: 50%; border: 2px solid var(--brand); flex: none; }

  /* preview strap */
  .strap-preview { left: 65px; top: 16px; width: 1065px; height: 42px; }
  .strap-preview .brand-row { position: absolute; inset: 0; display: flex; justify-content: space-around; align-items: center; }
  .strap-preview .brand { position: static; font-size: 15px; letter-spacing: 1.5px; gap: 6px; }
  .strap-preview .brand-dot { width: 16px; height: 16px; border-width: 1.5px; }

  /* main strap */
  .strap-main { left: 0; top: 266px; width: 1200px; height: 144px; }
  .strap-main .brand { left: 398px; top: 42px; height: 62px; gap: 22px; font-size: 46px; letter-spacing: 5px; }
  .strap-main .brand-dot { width: 62px; height: 62px; border-width: 4px; }
</style>
</head>
<body>
<main class="canvas">

  <section class="strap strap-preview" aria-label="Strap overview">
    <div class="strap-pattern" role="img" aria-label="Soft pink swirl ornament pattern"></div>
    <div class="panel" style="left:70px;width:14px"></div>
    <div class="panel mid" style="left:330px;width:90px"></div>
    <div class="panel" style="left:620px;width:12px"></div>
    <div class="panel mid" style="left:860px;width:95px"></div>
    <div class="trim trim-olive" style="top:3px;height:2px"></div>
    <div class="trim trim-olive" style="bottom:4px;height:2px"></div>
    <div class="brand-row">
      <div class="brand"><span class="brand-dot"></span>TAVONEST</div>
      <div class="brand"><span class="brand-dot"></span>TAVONEST</div>
      <div class="brand"><span class="brand-dot"></span>TAVONEST</div>
      <div class="brand"><span class="brand-dot"></span>TAVONEST</div>
      <div class="brand"><span class="brand-dot"></span>TAVONEST</div>
      <div class="brand"><span class="brand-dot"></span>TAVONEST</div>
    </div>
  </section>

  <section class="strap strap-main" aria-label="Crate strap">
    <div class="strap-pattern" role="img" aria-label="Soft pink swirl ornament pattern"></div>
    <div class="panel" style="left:369px;width:14px"></div>
    <div class="panel" style="left:436px;width:68px"></div>
    <div class="panel mid" style="left:504px;width:389px"></div>
    <div class="panel" style="left:690px;width:203px;opacity:.45"></div>
    <div class="trim trim-gold" style="top:10px;height:5px"></div>
    <div class="trim trim-olive" style="top:16px;height:3px"></div>
    <div class="trim trim-olive" style="top:123px;height:3px"></div>
    <div class="trim trim-gold" style="top:127px;height:6px"></div>
    <div class="brand"><span class="brand-dot"></span>TAVONEST</div>
  </section>

</main>
</body>
</html>
```